Mobile Fitness snd Therapy Business Card Design

I need a business card designed for my mobile fitness and therapy business.

Please view the images that I have uploaded. I like the simplicity of the design that I have attached. I adapted it with my information

Target Market(s)

Those seeking personal training, injury rehabilitation or massage therapy.

Industry/Entity Type

Business

Contact Information for Business Card

Derek Fulham - MSc, CAT(C), RMT, CSCS, Pn2
e-mail: derek@vantrelo.com
website: www.vantrelo.com
instagram: @derek_fulham

Font styles to use
Sans Serif

Colors
3176b5
0355a3

Requirements
Must have
• "Contact us to receive a FREE assessment"
• Services offered:
• Personal Training
• Golf Fitness
• Injury Rehab
• Massage Therapy
• Yoga
Nice to have
• Consistent colours with brand
• - Dark Blue: #232837
• - Blue: #5096f0
• Consistent look/feel with the website: www.vantrelo.com

```html
<!DOCTYPE html>
<html lang="en">
<head>
<meta charset="utf-8">
<title>Vantrelo Business Card</title>
<link href="https://fonts.googleapis.com/css2?family=Roboto:wght@400;500;700&family=Roboto+Condensed:wght@400;500;700&display=swap" rel="stylesheet">
<style>
  :root {
    --page-bg: #d9d6d0;
    --card-light: #f2f2f2;
    --card-light-edge: #e6e6e6;
    --navy: #232837;
    --ink: #1f2433;
    --brand-blue: #2b5fd9;
    --label-blue: #3a6fe6;
    --grey-text: #6b6e75;
    --white: #ffffff;
  }
  * { box-sizing: border-box; margin: 0; padding: 0; }
  html, body {
    width: 1200px; height: 886px; overflow: hidden;
    background: var(--page-bg);
    font-family: "Roboto", Arial, sans-serif;
  }
  .sheet {
    position: relative; width: 1200px; height: 886px;
    display: flex; flex-direction: column; align-items: center;
    justify-content: center; gap: 36px;
  }
  .card {
    position: relative; width: 630px; height: 360px;
    border-radius: 22px; overflow: hidden;
    box-shadow: 0 10px 26px rgba(0,0,0,0.18);
  }

  /* Front */
  .card-front {
    background: linear-gradient(135deg, var(--card-light-edge), var(--white) 55%, var(--card-light));
    display: flex; flex-direction: column; align-items: center;
  }
  .brand {
    margin-top: 108px;
    display: flex; align-items: center; gap: 14px;
  }
  .brand-square {
    width: 30px; height: 30px; background: var(--ink);
  }
  .brand-name {
    font-family: "Roboto", Arial, sans-serif;
    font-weight: 700; font-size: 58px; letter-spacing: 6px;
    color: var(--ink); line-height: 1;
  }
  .cta {
    margin-top: 70px;
    background: var(--brand-blue); color: var(--white);
    border-radius: 999px; padding: 6px 22px;
    font-family: "Roboto Condensed", Arial, sans-serif;
    font-weight: 700; font-size: 21px; letter-spacing: 0.3px;
    text-transform: uppercase;
  }
  .services {
    margin-top: 8px;
    font-size: 15px; color: var(--grey-text);
    display: flex; gap: 6px;
  }
  .services .sep { color: var(--brand-blue); }

  /* Back */
  .card-back { background: var(--navy); }
  .contact {
    position: absolute; left: 52px; top: 70px;
    font-family: "Roboto Condensed", Arial, sans-serif;
    text-transform: uppercase;
  }
  .person-name {
    color: var(--label-blue); font-weight: 500; font-size: 32px; line-height: 1;
  }
  .credentials {
    color: var(--label-blue); font-size: 13px; margin-top: 4px; letter-spacing: 0.3px;
  }
  .contact-item { margin-top: 26px; }
  .contact-label {
    color: var(--label-blue); font-weight: 500; font-size: 17px; line-height: 1.1;
  }
  .contact-value {
    color: var(--white); font-size: 19px; line-height: 1.2;
  }
</style>
</head>
<body>
<main class="sheet">
  <section class="card card-front" aria-label="Card front">
    <div class="brand">
      <span class="brand-square" aria-hidden="true"></span>
      <span class="brand-name">VANTRELO</span>
    </div>
    <p class="cta">Contact us to receive a free assessment</p>
    <p class="services">
      <span>Personal Training</span><span class="sep">|</span>
      <span>Golf Fitness</span><span class="sep">|</span>
      <span>Injury Rehab</span><span class="sep">|</span>
      <span>Massage Therapy</span><span class="sep">|</span>
      <span>Yoga</span>
    </p>
  </section>

  <section class="card card-back" aria-label="Card back">
    <div class="contact">
      <h1 class="person-name">Derek Fulham</h1>
      <p class="credentials">MSc, CAT(C), RMT, CSCS, Pn2</p>
      <div class="contact-item">
        <p class="contact-label">Email</p>
        <p class="contact-value">derek@vantrelo.com</p>
      </div>
      <div class="contact-item">
        <p class="contact-label">Web</p>
        <p class="contact-value">www.vantrelo.com</p>
      </div>
      <div class="contact-item">
        <p class="contact-label">Instagram</p>
        <p class="contact-value">@derek_fulham</p>
      </div>
    </div>
  </section>
</main>
</body>
</html>
```